New Bicycle shop business card

Hi!
I'm looking for a business card for my new proffesional bike mechanics shop. This shop is only for fixing broken bikes and not selling bikes.
Peferbly a modern and sleek and modern design.
Colors: black, grey, red, white
Information:
Name: Rijwielwerkplaats Vanhoutte
Shop owner: Bart Vanhoutte & Marieke Segers
Website: www.rijwielwerkplaats-vanhoutte.be
Email: info@rijwielwerkplaats-vanhoutte.be
Phone number: +32471902368
Street adres: Kerkweg 46
9940 Bellebeke
Slogan/shop information: Herstellingen van alle merken.
Logo: see files.
Target Market(s)
People who seek a mechanic to fix or upgrade their bikes.
Contact Information for Business Card
Information:
Website: info@rijwielwerkplaats-vanhoutte.be
9940 Bellebeke
Logo: see files.

```html
<!DOCTYPE html>
<html lang="nl">
<head>
<meta charset="utf-8">
<title>Rijwielwerkplaats Vanhoutte – visitekaartje</title>
<link rel="stylesheet" href="https://fonts.googleapis.com/css2?family=Roboto:wght@300;400;700&display=swap">
<style>
  :root {
    --backdrop: #3b3b3b;
    --card: #231d1c;
    --red: #d6293b;
    --white: #f2f0ee;
    --grey: #c9c5c2;
  }
  * { margin: 0; padding: 0; box-sizing: border-box; }
  html, body { width: 1200px; height: 901px; overflow: hidden; }
  body {
    background: var(--backdrop);
    font-family: "Roboto", Arial, sans-serif;
    display: flex;
    flex-direction: column;
    align-items: center;
    justify-content: center;
    gap: 56px;
  }
  .card {
    position: relative;
    width: 630px;
    height: 360px;
    background: var(--card);
    box-shadow: 0 10px 24px rgba(0,0,0,.35);
    overflow: hidden;
  }
  .brand {
    display: flex;
    align-items: center;
    gap: 12px;
  }
  .brand-mark {
    width: 22px;
    height: 22px;
    background: var(--red);
    flex: none;
  }
  .brand-name {
    color: var(--white);
    font-weight: 700;
    text-transform: uppercase;
    letter-spacing: 2px;
    font-size: 19px;
  }

  /* back side */
  .card-back { display: flex; align-items: center; justify-content: center; }
  .card-back .brand-name { font-size: 26px; letter-spacing: 3px; }
  .card-back .brand-mark { width: 30px; height: 30px; }

  /* front side */
  .card-front { padding: 38px 44px; }
  .card-front .brand { margin-bottom: 34px; }
  .details { padding-left: 150px; }
  .shop-name {
    color: var(--red);
    font-size: 25px;
    font-weight: 400;
    line-height: 1.1;
  }
  .owners {
    color: var(--grey);
    font-size: 13px;
    font-weight: 300;
    margin-top: 4px;
  }
  .address {
    color: var(--grey);
    font-size: 13px;
    font-weight: 300;
    line-height: 1.35;
    margin-top: 18px;
  }
  .contact-icons { display: flex; gap: 10px; margin-top: 14px; }
  .contact-icons svg { width: 12px; height: 12px; fill: var(--red); }
  .contact-list {
    list-style: none;
    color: var(--grey);
    font-size: 13px;
    font-weight: 300;
    line-height: 1.45;
    margin-top: 8px;
  }
  .slogan-band {
    position: absolute;
    left: 0; right: 0; bottom: 0;
    height: 30px;
    background: var(--red);
    color: var(--white);
    font-size: 12px;
    font-weight: 400;
    display: flex;
    align-items: center;
    justify-content: flex-end;
    padding-right: 44px;
  }
</style>
</head>
<body>

  <section class="card card-back" aria-label="Achterkant visitekaartje">
    <div class="brand">
      <span class="brand-mark"></span>
      <span class="brand-name">Rijwielwerkplaats Vanhoutte</span>
    </div>
  </section>

  <section class="card card-front" aria-label="Voorkant visitekaartje">
    <div class="brand">
      <span class="brand-mark"></span>
      <span class="brand-name">Rijwielwerkplaats Vanhoutte</span>
    </div>
    <div class="details">
      <h1 class="shop-name">Rijwielwerkplaats Vanhoutte</h1>
      <p class="owners">Owner: Bart Vanhoutte &amp; Marieke Segers</p>
      <p class="address">Kerkweg 46<br>9940 Bellebeke</p>
      <div class="contact-icons">
        <svg viewBox="0 0 24 24" aria-label="Telefoon" role="img"><path d="M6.6 10.8a15 15 0 0 0 6.6 6.6l2.2-2.2a1 1 0 0 1 1-.25 11.4 11.4 0 0 0 3.6.57 1 1 0 0 1 1 1V20a1 1 0 0 1-1 1A17 17 0 0 1 3 4a1 1 0 0 1 1-1h3.5a1 1 0 0 1 1 1c0 1.25.2 2.45.57 3.57a1 1 0 0 1-.25 1z"/></svg>
        <svg viewBox="0 0 24 24" aria-label="E-mail" role="img"><path d="M2 5h20v14H2z M2 5l10 8 10-8" /></svg>
        <svg viewBox="0 0 24 24" aria-label="Website" role="img"><circle cx="12" cy="12" r="10"/></svg>
      </div>
      <ul class="contact-list">
        <li>+32471902368</li>
        <li>info@rijwielwerkplaats-vanhoutte.be</li>
        <li>www.rijwielwerkplaats-vanhoutte.be</li>
      </ul>
    </div>
    <div class="slogan-band">Herstellingen van alle merken.</div>
  </section>

</body>
</html>
```